Retail Jewelry Business Card Design Project

We are in need of a new business card design for a retail jewelry store. This store is in the business of fine jewelry including but not specific to bridal jewelry, diamonds, designer jewelry and watches.

This store has been in business for 20 years but continues to strive for a modern professional appeal. The main colors use for this business are a royal blue, white and silver.

Target Market(s)

Target market is ages 18-50

Industry/Entity Type

Jewelry

Requirements
Must have
• Sales Person Name
Sales Person Email Address

Store Address
Store Phone
Website

Standard business card size. No odd shapes or sizes.
Nice to have
• Overall modern feel for card.

We have thought that a design with a nice feature of the logo on the back of the card would be nice but open to ideas.
Should not have
• No specific images of jewelry should be used.

```html
<!DOCTYPE html>
<html lang="en">
<head>
<meta charset="utf-8">
<title>Marlow Reed Fine Jewelry – Business Cards</title>
<link rel="stylesheet" href="https://fonts.googleapis.com/css2?family=Libre+Baskerville:ital,wght@0,400;0,700;1,700&family=Arimo:wght@400&display=swap">
<style>
  :root {
    --royal: #2b2f8f;
    --navy: #23236e;
    --lavender: #7a78c2;
    --white: #ffffff;
    --ink: #3a3a3a;
    --silver: #e4e6ee;
    --backdrop: #eeeef2;
  }
  * { box-sizing: border-box; margin: 0; padding: 0; }
  html, body { width: 1200px; height: 804px; overflow: hidden; }
  body {
    background: var(--backdrop);
    display: flex; align-items: center; justify-content: center; gap: 40px;
    font-family: "Libre Baskerville", Georgia, serif;
  }
  .card {
    position: relative; width: 560px; height: 320px; overflow: hidden;
    box-shadow: 0 2px 8px rgba(0,0,0,.15);
  }

  /* Front */
  .card-front { background: var(--white); }
  .brand {
    position: absolute; left: 0; right: 0; text-align: center;
    color: var(--navy); font-weight: 400;
  }
  .card-front .brand-name { top: 34px; font-size: 46px; }
  .card-front .brand-line { top: 98px; font-size: 17px; letter-spacing: 4px; text-transform: uppercase; }
  .rule { position: absolute; left: 0; right: 0; background: var(--navy); height: 2px; }
  .band { position: absolute; left: 0; right: 0; background: var(--lavender); }
  .rule-top { top: 128px; }
  .band-top { top: 130px; height: 8px; }
  .name-tab {
    position: absolute; top: 138px; left: 130px; width: 300px; height: 26px;
    background: var(--lavender); color: var(--white);
    font-style: italic; font-weight: 700; font-size: 14px;
    display: flex; align-items: center; justify-content: center; letter-spacing: .5px;
  }
  .divider { position: absolute; left: 262px; top: 176px; width: 1px; height: 84px; background: #b8b8c8; }
  .contact { position: absolute; left: 276px; top: 176px; list-style: none; font-size: 12.5px; color: var(--ink); }
  .contact li { display: flex; align-items: center; gap: 7px; height: 22px; }
  .contact svg { width: 12px; height: 12px; flex: none; }
  .band-low { top: 226px; height: 18px; border-top: 2px solid var(--navy); border-bottom: 2px solid var(--navy); right: auto; width: 262px; }
  .address { position: absolute; left: 116px; top: 256px; font-size: 12.5px; line-height: 1.6; color: var(--ink); font-style: normal; }

  /* Back */
  .card-back { background: var(--royal); }
  .card-back .brand { color: var(--white); }
  .card-back .brand-name { top: 96px; font-size: 52px; }
  .card-back .brand-line { top: 168px; font-size: 19px; letter-spacing: 5px; text-transform: uppercase; }
  .web-back {
    position: absolute; left: 0; right: 0; top: 262px; text-align: center;
    color: var(--silver); font-family: "Arimo", Arial, sans-serif; font-size: 15px; letter-spacing: 3px;
  }
</style>
</head>
<body>
  <section class="card card-front" aria-label="Business card front">
    <div class="brand brand-name">Marlow Reed</div>
    <div class="brand brand-line">Fine Jewelry</div>
    <div class="rule rule-top"></div>
    <div class="band band-top"></div>
    <div class="name-tab">Marlow Reed Ellison</div>
    <div class="divider"></div>
    <ul class="contact">
      <li>
        <svg viewBox="0 0 12 12"><circle cx="6" cy="6" r="6" fill="#23236e"/><path d="M4 3.2l1 1-.6.8c.4.9 1.1 1.6 2 2l.8-.6 1 1-.7.9C5.6 8.2 3.8 6.4 3.7 4z" fill="#fff"/></svg>
        555-014-2290
      </li>
      <li>
        <svg viewBox="0 0 12 12"><circle cx="6" cy="6" r="6" fill="#23236e"/><rect x="3" y="4" width="6" height="4" fill="#fff"/><path d="M3 4l3 2.2L9 4" stroke="#23236e" stroke-width=".7" fill="none"/></svg>
        marlow@marlowreedjewelry.com
      </li>
      <li>
        <svg viewBox="0 0 12 12"><circle cx="6" cy="6" r="6" fill="#23236e"/><circle cx="6" cy="6" r="3.2" stroke="#fff" stroke-width=".7" fill="none"/><path d="M2.8 6h6.4M6 2.8v6.4" stroke="#fff" stroke-width=".7"/></svg>
        www.marlowreedjewelry.com
      </li>
    </ul>
    <div class="band band-low"></div>
    <address class="address">2270 Larkin Street<br>Bay Harbor, FL 32499</address>
  </section>

  <section class="card card-back" aria-label="Business card back">
    <div class="brand brand-name">Marlow Reed</div>
    <div class="brand brand-line">Fine Jewelry</div>
    <div class="web-back">www.marlowreedjewelry.com</div>
  </section>
</body>
</html>
```